Design 4 pages for an event discovery website

This is a contest for the design of 4 pages for an events discovery website. The feature is part of the new sign-up process.

Please see the attached document for a full scope, mockups and the parent category icons.

Target Market(s)

18-35 Australian event goers

Industry/Entity Type

Events

Number of Pages Required

4 page

```html
<!DOCTYPE html>
<html lang="en">
<head>
<meta charset="utf-8">
<title>Evenlo – Step 1 of 5</title>
<link href="https://fonts.googleapis.com/css2?family=Raleway:wght@300;400;500&family=Open+Sans:wght@400&display=swap" rel="stylesheet">
<style>
  :root {
    --header-top: #3a88d2;
    --header-bottom: #1451a8;
    --navy: #0f3a70;
    --heading: #1b4f8f;
    --link: #1a4a9c;
    --orange: #ff9000;
    --text: #333333;
    --white: #ffffff;
    --tick: #b3b3b3;
    --footer-bg: #efefef;
    --footer-line: #c9c9c9;
    --footer-icon: #6a6a6a;
    --chirpa-a: #28c8ef;
    --chirpa-b: #10b4e6;
    --pictura-a: #8a5a4a;
    --pictura-b: #6b3f31;
    --tunewave-a: #7dc451;
    --tunewave-b: #55a42c;
    --melodia-a: #4a4a4a;
    --melodia-b: #1c1c1c;
  }
  * { margin: 0; padding: 0; box-sizing: border-box; }
  html, body { width: 1200px; height: 570px; overflow: hidden; background: var(--white); }
  body { position: relative; font-family: "Open Sans", sans-serif; color: var(--text); }

  .site-header {
    position: absolute; left: 0; top: 0; width: 1200px; height: 96px;
    background: linear-gradient(var(--header-top), var(--header-bottom));
  }
  .brand {
    position: absolute; left: 141px; top: 14px;
    font-family: "Raleway", sans-serif; font-weight: 300; font-size: 48px;
    color: var(--white); letter-spacing: -0.5px;
  }
  .nav-link {
    position: absolute; left: 345px; top: 37px;
    font-family: "Raleway", sans-serif; font-weight: 400; font-size: 18px; color: var(--white);
  }
  .search {
    position: absolute; left: 688px; top: 37px; width: 196px; height: 28px;
    background: var(--white); border: 2px solid #d5dde8; border-radius: 14px;
    font-size: 10px; color: #555; padding: 7px 0 0 15px;
  }
  .search svg { position: absolute; right: 10px; top: 6px; }
  .btn-pill {
    position: absolute; top: 36px; height: 29px; border-radius: 15px;
    font-family: "Raleway", sans-serif; font-weight: 500; font-size: 13px; color: var(--white);
    display: flex; align-items: center; justify-content: center;
  }
  .btn-signup { left: 907px; width: 74px; background: var(--navy); }
  .btn-login { left: 987px; width: 74px; background: var(--orange); }

  .step-title {
    position: absolute; left: 141px; top: 132px;
    font-family: "Raleway", sans-serif; font-weight: 300; font-size: 37px; color: var(--heading);
  }
  .step-copy { position: absolute; left: 143px; font-size: 13px; color: var(--text); }
  .copy-1 { top: 186px; }
  .copy-2 { top: 213px; }

  .account-btn {
    position: absolute; left: 142px; width: 179px; height: 42px; border-radius: 2px;
    display: flex; align-items: center; color: var(--white);
    font-family: "Raleway", sans-serif; font-weight: 500; font-size: 18px;
  }
  .account-btn .icon-slot {
    width: 49px; height: 100%; display: flex; align-items: center; justify-content: center;
    border-right: 1px solid rgba(255,255,255,0.35);
  }
  .account-btn .icon-slot span { width: 18px; height: 18px; border-radius: 50%; background: var(--white); }
  .account-btn .label { padding-left: 21px; }
  .btn-chirpa { top: 252px; background: linear-gradient(var(--chirpa-a), var(--chirpa-b)); }
  .btn-pictura { top: 305px; background: linear-gradient(var(--pictura-a), var(--pictura-b)); }
  .btn-tunewave { top: 359px; background: linear-gradient(var(--tunewave-a), var(--tunewave-b)); }
  .btn-melodia { top: 412px; background: linear-gradient(var(--melodia-a), var(--melodia-b)); }

  .status { position: absolute; left: 328px; display: flex; align-items: center; font-size: 11px; color: var(--link); }
  .status svg { margin-right: 8px; }
  .status-linked { top: 263px; }
  .status-requested { top: 373px; }
  .status-requested svg { margin-right: 14px; }

  .site-footer {
    position: absolute; left: 0; top: 509px; width: 1200px; height: 61px;
    background: var(--footer-bg); border-top: 1px solid var(--footer-line);
  }
  .legal { position: absolute; left: 141px; top: 20px; font-size: 11px; color: var(--text); word-spacing: 1px; }
  .footer-social { position: absolute; left: 975px; top: 20px; display: flex; gap: 6px; }
  .footer-social span { width: 19px; height: 19px; border-radius: 3px; background: var(--footer-icon); }
</style>
</head>
<body>
  <header class="site-header">
    <div class="brand">Evenlo</div>
    <div class="nav-link">Find Events</div>
    <div class="search">Search
      <svg width="14" height="14" viewBox="0 0 14 14" aria-hidden="true">
        <circle cx="5.8" cy="5.8" r="4.4" fill="none" stroke="#777" stroke-width="2"/>
        <line x1="9" y1="9" x2="12.6" y2="12.6" stroke="#777" stroke-width="2.2" stroke-linecap="round"/>
      </svg>
    </div>
    <div class="btn-pill btn-signup">Sign Up</div>
    <div class="btn-pill btn-login">Log In</div>
  </header>

  <main>
    <h1 class="step-title">Step 1 of 5</h1>
    <p class="step-copy copy-1">Link in all your other Social media accounts and Music players</p>
    <p class="step-copy copy-2">By Linking your accounts, we can save you a lot of time by automactically determing your intrests</p>

    <div class="account-btn btn-chirpa"><div class="icon-slot"><span></span></div><div class="label">chirpa</div></div>
    <div class="status status-linked">
      <svg width="20" height="20" viewBox="0 0 20 20" aria-hidden="true"><circle cx="10" cy="10" r="10" fill="var(--tick)"/><path d="M5.5 10.3l3 3 6-6.3" fill="none" stroke="#fff" stroke-width="2.4" stroke-linecap="round" stroke-linejoin="round"/></svg>
      Linked
    </div>

    <div class="account-btn btn-pictura"><div class="icon-slot"><span></span></div><div class="label">pictura</div></div>

    <div class="account-btn btn-tunewave"><div class="icon-slot"><span></span></div><div class="label">tunewave</div></div>
    <div class="status status-requested">
      <svg width="20" height="20" viewBox="0 0 20 20" aria-hidden="true"><circle cx="10" cy="10" r="10" fill="var(--tick)"/><path d="M5.5 10.3l3 3 6-6.3" fill="none" stroke="#fff" stroke-width="2.4" stroke-linecap="round" stroke-linejoin="round"/></svg>
      We don't have that future yet but have requested your interest
    </div>

    <div class="account-btn btn-melodia"><div class="icon-slot"><span></span></div><div class="label">melodia</div></div>
  </main>

  <footer class="site-footer">
    <div class="legal">© 2015 Company Name &nbsp;All right reserved &nbsp;Term of Use</div>
    <div class="footer-social"><span></span><span></span><span></span></div>
  </footer>
</body>
</html>
```